Distribution/Printing company needs a web site to inform prospective customers on what we do.

Distribution/Printing/Packaging company needs a web site to inform prospective customers on what we do. Please look at our direct to consumer web site (under development) for an idea of the product lines we sell: storedev.maplewickhaven.com
Logo files are attached as is a flyer that is under development which contains other information about the company (this is to be used for content- not to be posted as is). The web site should be focused on our business customer base and is not intended to be direct to consumer. Site should have a link to our consumer web site.
Site design should be mobile friendly, or mobile could be redirected to a mobile version. This web site will be strictly informational and will not be designed for any sales transactions.

Target Market(s)

Manufacturing and retail businesses, any other multi-site business that would benefit from centralized pricing and budget controls we can provide (banks, medical/dental offices, educational facilities, etc).

Industry/Entity Type

It Company

Coding

Coded - Design and coding required

Number of Pages Required

5+ page

Requirements
Must have
• 1) Top level menu: Products, about us, locations, contact us, news
• 2) page with news/promotions that is easily updated
• 3) "contact us" form (name, company, phone, email address) email link
• 4) link to www.store.maplewickhaven.com with information that lower pricing is available for businesses
• 5) SEO keywords
• 6) Link to powerpoint presentation file
Nice to have
• 1) our phone number should appear on every page near the top

```html
<!DOCTYPE html>
<html lang="en">
<head>
<meta charset="utf-8">
<title>Maplewick Haven Supply – Packaging, Printing, Distribution</title>
<link rel="stylesheet" href="https://fonts.googleapis.com/css2?family=Montserrat:wght@400;500;600;700&family=Arimo:wght@400;700&display=swap">
<style>
:root{
  --red:#b3060c;
  --dark:#262626;
  --footer:#1e1e1e;
  --white:#ffffff;
  --ink:#2b2b2b;
  --body:#444444;
  --muted:#9a9a9a;
  --line:#d9d9d9;
  --grey-btn:#dcdcdc;
}
*{box-sizing:border-box;margin:0;padding:0}
html,body{width:1200px;height:2624px;overflow:hidden;background:var(--white)}
body{font-family:"Arimo",Arial,sans-serif;color:var(--body);position:relative}
.section{position:absolute;left:0;width:1200px}
.abs{position:absolute}
.heading{font-family:"Montserrat",Arial,sans-serif;font-weight:600;text-transform:uppercase}
.section-title{position:absolute;left:0;width:1200px;text-align:center;font-family:"Montserrat",Arial,sans-serif;font-weight:600;font-size:30px;letter-spacing:.5px}
.title-rule{position:absolute;left:502px;width:196px;height:2px}
.title-rule::after{content:"";position:absolute;left:84px;top:-1px;width:28px;height:4px;background:var(--red)}

/* hero */
.hero{top:0;height:680px;background:linear-gradient(100deg,#3b352f 0%,#5a4a3a 35%,#6e5943 60%,#3e3a36 100%)}
.hero-photo{position:absolute;inset:0;background:radial-gradient(ellipse at 72% 55%,rgba(150,120,90,.55),transparent 60%),linear-gradient(180deg,rgba(0,0,0,.15),rgba(0,0,0,.35))}
.topbar{position:absolute;left:0;top:0;width:1200px;height:166px;background:rgba(20,20,20,.55)}
.brand{position:absolute;left:100px;top:88px;color:var(--white);white-space:nowrap}
.brand-name{font-family:"Montserrat",Arial,sans-serif;font-weight:700;font-size:17px;letter-spacing:.2px;line-height:22px}
.brand-tag{font-family:"Montserrat",Arial,sans-serif;font-size:11.5px;font-weight:500;margin-top:2px;text-align:center}
.nav{position:absolute;top:84px;left:0;width:1200px;height:32px;font-family:"Montserrat",Arial,sans-serif;font-size:15px;color:var(--white)}
.nav a{color:var(--white);text-decoration:none;position:absolute;top:0;height:32px;line-height:32px;white-space:nowrap}
.nav .login{border:1.5px solid var(--white);width:96px;line-height:29px;text-align:center}
.nav .search{display:flex;align-items:center}
.hero-title{position:absolute;top:296px;left:0;width:1200px;text-align:center;color:var(--white);font-family:"Montserrat",Arial,sans-serif;font-weight:500;font-size:38px;line-height:52px}
.hero-sub{position:absolute;top:420px;left:0;width:1200px;text-align:center;color:var(--white);font-size:16px;font-weight:700}
.btn{position:absolute;display:block;text-align:center;font-family:"Montserrat",Arial,sans-serif;font-weight:600;text-decoration:none}
.btn-red{background:var(--red);color:var(--white)}
.btn-grey{background:var(--grey-btn);color:var(--red)}
.hero .btn{height:51px;line-height:51px;font-size:15px;width:194px;top:481px}
.slide-arrow{position:absolute;top:334px}

/* welcome */
.welcome{top:680px;height:328px}
.welcome-photo{left:100px;top:46px;width:304px;height:224px;background:linear-gradient(90deg,#7a5a3c 0%,#b88a5a 30%,#e0b23a 50%,#b88a5a 70%,#6e5034 100%);box-shadow:0 16px 18px -10px rgba(0,0,0,.35)}
.welcome-title{left:434px;top:42px;font-size:27px;color:var(--ink);font-weight:700;white-space:nowrap}
.welcome-rule{left:434px;top:77px;width:563px;height:1px;background:var(--line)}
.welcome-rule::before{content:"";position:absolute;left:0;top:-1px;width:150px;height:3px;background:var(--red)}
.welcome-text{left:434px;top:100px;width:604px;font-size:11.5px;line-height:23px;color:var(--body)}
.welcome .btn{left:434px;top:235px;width:138px;height:38px;line-height:38px;font-size:14px}

/* features */
.features{top:1008px;height:306px;background:var(--dark);color:var(--white)}
.notch{position:absolute;left:568px;width:0;height:0;border-left:32px solid transparent;border-right:32px solid transparent;border-top:33px solid var(--dark)}
.features .section-title{top:48px;color:var(--white)}
.features .title-rule{top:95px;background:#8a8a8a}
.feature{position:absolute;top:128px}
.feature h3{font-family:"Montserrat",Arial,sans-serif;font-weight:500;font-size:19px;margin-bottom:12px}
.feature ul{list-style:none;font-size:11px;line-height:25.5px}
.feature li{position:relative;padding-left:45px}
.feature li.tick::before{content:"";position:absolute;left:22px;top:7px;width:11px;height:6px;border-left:2.5px solid var(--white);border-bottom:2.5px solid var(--white);transform:rotate(-45deg)}

/* what we do */
.services{top:1347px;height:407px}
.services .section-title{top:50px;color:var(--ink)}
.services .title-rule{top:99px;background:var(--line)}
.tile{position:absolute;top:145px;width:229px;height:206px;box-shadow:0 16px 16px -10px rgba(0,0,0,.3)}
.tile-label{position:absolute;left:0;bottom:0;width:100%;height:49px;line-height:49px;background:rgba(40,40,40,.72);color:var(--white);text-align:center;font-family:"Montserrat",Arial,sans-serif;font-size:11.5px;text-transform:uppercase}

/* products */
.products{top:1754px;height:467px;background:var(--dark)}
.products .section-title{top:40px;color:var(--white)}
.products .title-rule{top:88px;background:#8a8a8a}
.card{position:absolute;top:126px;width:231px;height:271px;background:var(--white);border:1px solid #cfcfcf;text-align:center}
.card-photo{height:158px;border-bottom:1px solid #d5dde3}
.card h4{font-family:"Montserrat",Arial,sans-serif;font-weight:600;font-size:15px;color:var(--ink);margin:11px 0 5px}
.card p{font-size:11.3px;line-height:20.5px;color:var(--ink);padding:0 14px}

/* clients */
.clients{top:2221px;height:297px}
.clients .section-title{top:71px;color:var(--ink)}
.clients .title-rule{top:117px;background:var(--line)}
.client{position:absolute;top:154px;width:176px;height:100px;border:6px solid #eeeeee;display:flex;align-items:center;justify-content:center;gap:8px;font-family:"Arimo",Arial,sans-serif;font-size:19px;font-weight:700;color:#3a3a3a}
.client-dot{width:12px;height:12px;border-radius:50%;background:#3a3a3a}

/* footer */
.footer{top:2518px;height:106px;background:var(--footer);color:#e6e6e6;font-size:11.5px}
.footer-links{position:absolute;left:98px;top:24px;display:flex}
.footer-links a{color:#e6e6e6;text-decoration:none;margin-right:6px}
.socials{position:absolute;left:98px;top:52px;display:flex;gap:6px}
.social{width:28px;height:28px;border:1.5px solid #cfcfcf;border-radius:50%}
.copyright{position:absolute;left:780px;top:42px}
.build{position:absolute;left:1142px;top:42px}
</style>
</head>
<body>

<header class="section hero">
  <div class="hero-photo" role="img" aria-label="Warehouse worker taping a cardboard box, staff and shelving blurred behind"></div>
  <div class="topbar"></div>
  <div class="brand">
    <div class="brand-name">MAPLEWICK HAVEN SUPPLY</div>
    <div class="brand-tag">Packaging • Printing • Distribution</div>
  </div>
  <nav class="nav">
    <a style="left:519px">Home</a>
    <a style="left:624px">Shop ⌄</a>
    <a style="left:735px">About</a>
    <a style="left:846px">Contact</a>
    <a class="login" style="left:941px">Login</a>
    <a class="search" style="left:1086px">
      <svg width="16" height="16" viewBox="0 0 16 16" aria-hidden="true"><circle cx="6.5" cy="6.5" r="4.5" fill="none" stroke="#fff" stroke-width="2"/><path d="M10 10l4.5 4.5" stroke="#fff" stroke-width="2.4"/></svg>
    </a>
  </nav>
  <svg class="slide-arrow" style="left:44px" width="22" height="56" viewBox="0 0 22 56" aria-hidden="true"><path d="M20 2 L3 28 L20 54" fill="none" stroke="#ddd" stroke-width="1.5"/></svg>
  <svg class="slide-arrow" style="left:1138px" width="22" height="56" viewBox="0 0 22 56" aria-hidden="true"><path d="M2 2 L19 28 L2 54" fill="none" stroke="#ddd" stroke-width="1.5"/></svg>
  <h1 class="hero-title">NOW, YOU REALLY CAN GET EVERYTHING<br>IN ONE STOP</h1>
  <p class="hero-sub">We offer you simple, economical, practical, functional generic and customized goods to carry</p>
  <a class="btn btn-red" style="left:376px">View more Products</a>
  <a class="btn btn-grey" style="left:591px">See Our Pricing</a>
</header>

<section class="section welcome">
  <div class="abs welcome-photo" role="img" aria-label="Warehouse aisle with stacked cartons and a yellow forklift"></div>
  <h2 class="abs heading welcome-title">WELCOME TO&nbsp; MAPLEWICK HAVEN SUPPLY</h2>
  <div class="abs welcome-rule"></div>
  <p class="abs welcome-text">Lorem Ipsum is simply dummy text of the printing and typesetting industry. Lorem Ipsum has been the industry's standard dummy text ever since the 1500s, when an unknown printer took a galley of type and scrambled it to make a type specimen book. It has survived not only five centuries, but also the leap into electronic typesetting, remaining essentially unchanged. It was popularised in the 1960s with the release of Lettrix sheets containing Lorem Ipsum passages, and more recently with desktop publishing software like Pagecraft Studio.</p>
  <a class="btn btn-red">View more info</a>
</section>

<section class="section features">
  <h2 class="section-title">INCREDIBLE FEATURES</h2>
  <div class="title-rule"></div>
  <svg class="abs" style="left:38px;top:142px" width="10" height="22" viewBox="0 0 10 22" aria-hidden="true"><path d="M9 1 L2 11 L9 21" fill="none" stroke="#444" stroke-width="1.3"/></svg>
  <svg class="abs" style="left:1140px;top:142px" width="10" height="22" viewBox="0 0 10 22" aria-hidden="true"><path d="M1 1 L8 11 L1 21" fill="none" stroke="#444" stroke-width="1.3"/></svg>
  <div class="feature" style="left:98px">
    <h3>Consolidate your spend on one platform!</h3>
    <ul>
      <li class="tick">Order items from MHS, or manage orders for your Customer Owned inventory.</li>
      <li>Manage orders for outside vendors</li>
      <li class="tick">Managed "Passthrough" items set up with a maintenance fee – i.e. $x.xx per item, per month.</li>
      <li class="tick">Managed "Passthrough" items set up with a transaction fee – i.e. $x.xx per item, per transaction.</li>
    </ul>
  </div>
  <div class="feature" style="left:673px">
    <h3>Order Receipt Verification</h3>
    <ul>
      <li class="tick">Receive all inbound orders via the system.</li>
      <li class="tick">Verify that quantities stated to be shipped by supplier are actually<br>received by location.</li>
    </ul>
  </div>
  <div class="notch" style="top:306px"></div>
</section>

<section class="section services">
  <h2 class="section-title">WHAT WE DO</h2>
  <div class="title-rule"></div>
  <div class="tile" style="left:100px;background:linear-gradient(160deg,#8a6a48,#c89a66 45%,#5d4a3a)" role="img" aria-label="Staff packing cartons in a warehouse"><div class="tile-label">Packaging</div></div>
  <div class="tile" style="left:359px;background:linear-gradient(160deg,#f4f4f4,#e4d6c2 50%,#b88e62)" role="img" aria-label="Businessman leaning on stacked boxes"><div class="tile-label">Printing</div></div>
  <div class="tile" style="left:616px;background:linear-gradient(160deg,#d8d8d4,#b8a58a 50%,#6a6560)" role="img" aria-label="Courier unloading a box from a delivery van"><div class="tile-label">Distribution</div></div>
  <div class="tile" style="left:871px;background:linear-gradient(160deg,#cfcfd2,#9c7d70 50%,#a93c34)" role="img" aria-label="Tall warehouse racking with red shelves"><div class="tile-label">Consequatur perferendis</div></div>
</section>

<section class="section products">
  <div class="notch" style="top:-1px;border-top-color:var(--white)"></div>
  <h2 class="section-title">OUR PRODUCT</h2>
  <div class="title-rule"></div>
  <article class="card" style="left:98px">
    <div class="card-photo" role="img" aria-label="Stacked red, blue and yellow storage bins" style="background:linear-gradient(120deg,#fff 10%,#d6322c 30%,#2b5fb0 50%,#e6c21e 70%,#fff 90%)"></div>
    <h4>Storage</h4>
    <p>Lorem Ipsum is simply dummy text of the printing and typesetting industry. Lorem Ipsum has been the industry's</p>
  </article>
  <article class="card" style="left:355px">
    <div class="card-photo" role="img" aria-label="Calculator, stapler and pen holder" style="background:linear-gradient(120deg,#fff 15%,#4a4a4a 40%,#9a9a9a 60%,#fff 85%)"></div>
    <h4>Office</h4>
    <p>Lorem Ipsum is simply dummy text of the printing and typesetting industry. Lorem Ipsum has been the industry's</p>
  </article>
  <article class="card" style="left:610px">
    <div class="card-photo" role="img" aria-label="Red safety kit with warning triangle and tools" style="background:linear-gradient(120deg,#fff 15%,#c8201c 45%,#e28a2a 65%,#fff 88%)"></div>
    <h4>Industrial</h4>
    <p>Lorem Ipsum is simply dummy text of the printing and typesetting industry. Lorem Ipsum has been the industry's</p>
  </article>
  <article class="card" style="left:867px">
    <div class="card-photo" role="img" aria-label="Assorted janitorial cleaning supplies and bucket" style="background:linear-gradient(120deg,#fff 15%,#3a6fb8 40%,#d9d9d9 60%,#d45a2a 75%,#fff 90%)"></div>
    <h4>Janitorial</h4>
    <p>Lorem Ipsum is simply dummy text of the printing and typesetting industry. Lorem Ipsum has been the industry's</p>
  </article>
  <div class="notch" style="top:467px"></div>
</section>

<section class="section clients">
  <h2 class="section-title">OUR CLIENTS</h2>
  <div class="title-rule"></div>
  <svg class="abs" style="left:38px;top:192px" width="10" height="22" viewBox="0 0 10 22" aria-hidden="true"><path d="M9 1 L2 11 L9 21" fill="none" stroke="#ccc" stroke-width="1.3"/></svg>
  <svg class="abs" style="left:1150px;top:192px" width="10" height="22" viewBox="0 0 10 22" aria-hidden="true"><path d="M1 1 L8 11 L1 21" fill="none" stroke="#ccc" stroke-width="1.3"/></svg>
  <div class="client" style="left:100px">Corvale</div>
  <div class="client" style="left:304px">Brightlane</div>
  <div class="client" style="left:509px"><span class="client-dot"></span>Tidewater</div>
  <div class="client" style="left:715px">Norhaven</div>
  <div class="client" style="left:922px">Kestrel Labs</div>
</section>

<footer class="section footer">
  <div class="footer-links">
    <a>Privacy Policy |</a><a>Store Locator |</a><a>Advanced Search |</a><a>Terms &amp; Conditions</a>
  </div>
  <div class="socials">
    <span class="social"></span><span class="social"></span><span class="social"></span><span class="social"></span><span class="social"></span>
  </div>
  <p class="copyright">Copyrights © 2015 maplewick haven supply&nbsp; . All rights reserved.</p>
  <p class="build">C12</p>
</footer>

</body>
</html>
```